Stylish new business card needed!

Hello everyone! I am in need of a new business card design for an alarm company here in Hurricane WV. I have all fonts, color codes and logos provided for you use! We are a young company and like the style of a clean sleek looking business card. Would like it double sided, one side holding the logo and the other with your design!
Target Market(s)
The people that are looking for the newest tech for home automation and security
Industry/Entity Type
Alarm services; Home automation
Contact Information for Business Card
Name of person; position (Sales; Installer); Phone Number (555.418.7260); Employee cell Number; Website (www.GuardedByVelk.example); Employee Email; Double sided
Look and feel
Each slider illustrates characteristics of the customer's brand and the style your logo design should communicate.

```html
<!DOCTYPE html>
<html lang="en">
<head>
<meta charset="utf-8">
<title>Velk Business Card</title>
<link rel="stylesheet" href="https://fonts.googleapis.com/css2?family=Montserrat:wght@400;500;700&display=swap">
<style>
  :root {
    --stage: #c9c9c9;
    --card: #9a9a9a;
    --accent: #f2904e;
    --ink: #ffffff;
    --shadow: rgba(0,0,0,0.18);
  }
  * { margin: 0; padding: 0; box-sizing: border-box; }
  html, body { width: 1200px; height: 788px; overflow: hidden; }
  body {
    background: var(--stage);
    font-family: "Montserrat", Arial, sans-serif;
    display: flex;
    flex-direction: column;
    align-items: center;
    justify-content: center;
    gap: 40px;
  }
  .card {
    position: relative;
    width: 600px;
    height: 343px;
    background: var(--card);
    border-radius: 26px;
    box-shadow: 0 8px 24px var(--shadow);
    color: var(--ink);
  }
  .wordmark {
    display: flex;
    align-items: center;
    gap: 12px;
    font-weight: 500;
    color: var(--ink);
    letter-spacing: 0.04em;
    line-height: 1;
  }
  .wordmark-dot {
    border-radius: 50%;
    background: var(--accent);
    flex: none;
  }
  .card-front .wordmark {
    position: absolute;
    right: 70px;
    top: 52px;
    font-size: 72px;
  }
  .card-front .wordmark-dot { width: 18px; height: 18px; }
  .divider {
    position: absolute;
    left: 34px;
    right: 110px;
    top: 196px;
    height: 1px;
    background: var(--accent);
  }
  .identity {
    position: absolute;
    left: 34px;
    bottom: 155px;
  }
  .person-name {
    color: var(--accent);
    font-weight: 700;
    font-size: 22px;
    letter-spacing: 0.03em;
    text-transform: uppercase;
  }
  .person-role {
    font-size: 14px;
    margin-top: 4px;
  }
  .contact-list {
    position: absolute;
    left: 34px;
    top: 214px;
    list-style: none;
    font-size: 14px;
  }
  .contact-list li {
    display: flex;
    align-items: center;
    gap: 10px;
    margin-bottom: 8px;
  }
  .contact-icon { width: 13px; height: 13px; flex: none; }
  .address {
    position: absolute;
    right: 34px;
    top: 214px;
    text-align: right;
    font-size: 14px;
    line-height: 1.6;
  }
  .card-back {
    display: flex;
    align-items: center;
    justify-content: center;
  }
  .card-back .wordmark { font-size: 110px; gap: 20px; }
  .card-back .wordmark-dot { width: 28px; height: 28px; }
</style>
</head>
<body>
  <section class="card card-front" aria-label="Business card front">
    <div class="wordmark"><span class="wordmark-dot"></span>VELK</div>
    <div class="identity">
      <p class="person-name">Dana Whitfield</p>
      <p class="person-role">Sales/Installer</p>
    </div>
    <div class="divider"></div>
    <ul class="contact-list">
      <li>
        <svg class="contact-icon" viewBox="0 0 16 16" aria-hidden="true"><path fill="var(--accent)" d="M3.6 1.5l2.3 2.8-1.3 1.6c.9 2 2.6 3.7 4.6 4.6l1.6-1.3 2.8 2.3-1.3 2.2C7 13.4 2.6 9 1.4 2.8z"/></svg>
        <span>555.418.7260</span>
      </li>
      <li>
        <svg class="contact-icon" viewBox="0 0 16 16" aria-hidden="true"><rect x="1" y="3" width="14" height="10" fill="var(--accent)"/><path d="M1 3l7 6 7-6" fill="none" stroke="var(--card)" stroke-width="1.4"/></svg>
        <span>info@GuardedByVelk.example</span>
      </li>
      <li>
        <svg class="contact-icon" viewBox="0 0 16 16" aria-hidden="true"><g fill="none" stroke="var(--accent)" stroke-width="1.4"><circle cx="8" cy="8" r="6.5"/><ellipse cx="8" cy="8" rx="3" ry="6.5"/><path d="M1.5 8h13"/></g></svg>
        <span>www.GuardedByVelk.example</span>
      </li>
    </ul>
    <address class="address" style="font-style:normal">
      1480 W Harbor Lane<br>Marlow County Name 7702
    </address>
  </section>

  <section class="card card-back" aria-label="Business card back">
    <div class="wordmark"><span class="wordmark-dot"></span>VELK</div>
  </section>
</body>
</html>
```